Flowmark Engineering Business Card

our company has just rebranded and taken on a new logo design. We now need to update our business cards with the new logo. This is also an opportunity to reformat and modernize our look. We are an engineering company so the look needs to be formal and professional yet it should look modern. Have a look at our current card and the new card should have the same information.

Target Market(s)

Engineering firms, government, mining companies

Industry/Entity Type

Mechanical Engineering

Contact Information for Business Card

see example attached

Requirements
Must have
• look professional and modern
Should not have
• should not include the office locations 'Brisbane, Sydney and Kuala Lumpur'
• you will find this on the example but it should not be included in these versions. please remove from your submissions and resubmit

```html
<!DOCTYPE html>
<html lang="en">
<head>
<meta charset="utf-8">
<title>Flowmark Engineering Business Card</title>
<link rel="stylesheet" href="https://fonts.googleapis.com/css2?family=Exo+2:wght@400;500;600&display=swap">
<style>
  :root {
    --page-bg: #e4e6ea;
    --card-top: #f7f8fa;
    --card-bottom: #eceef2;
    --brand-blue: #3b4bb0;
    --band-blue: #3c4fb8;
    --band-edge: #2a3580;
    --icon-fill: #d9dde8;
    --icon-glyph: #3c4fb8;
    --white: #ffffff;
    --footer-light: #f1f2f4;
    --footer-mid: #c9ccd2;
    --footer-text: #2b2f3a;
    --silver-line: #9ea3ad;
  }
  * { margin: 0; padding: 0; box-sizing: border-box; }
  html, body {
    width: 1200px; height: 769px; overflow: hidden;
    background: var(--page-bg);
    font-family: "Exo 2", sans-serif;
  }
  .card {
    position: absolute; left: 50px; top: 65px;
    width: 1100px; height: 640px;
    background: linear-gradient(180deg, var(--card-top), var(--card-bottom));
    box-shadow: 0 10px 30px rgba(0,0,0,.15);
    overflow: hidden;
  }
  .brand {
    position: absolute; left: 240px; top: 44px;
    display: flex; align-items: center; gap: 22px;
  }
  .brand-mark {
    width: 118px; height: 118px; border-radius: 50%;
    border: 8px solid var(--brand-blue);
  }
  .brand-name { color: var(--brand-blue); font-weight: 500; line-height: 1; }
  .brand-name .primary { display: block; font-size: 72px; letter-spacing: 2px; }
  .brand-name .secondary {
    display: flex; align-items: center; gap: 12px;
    font-size: 30px; letter-spacing: 7px; margin-top: 8px;
  }
  .brand-name .secondary::before,
  .brand-name .secondary::after {
    content: ""; flex: 1; height: 3px; background: var(--brand-blue);
  }
  .contact-band {
    position: absolute; left: 0; top: 228px; width: 100%; height: 300px;
    background: var(--band-blue);
    border-top: 6px solid var(--band-edge);
    border-bottom: 6px solid var(--band-edge);
    color: var(--white);
  }
  .contact-item {
    position: absolute; top: 52px; width: 360px; margin-left: -180px;
    text-align: center;
  }
  .contact-item .icon {
    width: 96px; height: 96px; border-radius: 50%;
    background: var(--icon-fill); border: 4px solid var(--white);
    margin: 0 auto 34px; display: flex; align-items: center; justify-content: center;
  }
  .contact-item .icon svg { width: 56px; height: 56px; }
  .person-name { font-size: 44px; font-weight: 500; letter-spacing: 1px; line-height: 1; }
  .person-role { font-size: 16px; letter-spacing: 1px; margin-top: 8px; }
  .contact-line { font-size: 27px; letter-spacing: 1px; line-height: 40px; }
  .footer {
    position: absolute; left: 0; top: 528px; width: 100%; height: 112px;
    background: linear-gradient(90deg, var(--footer-mid), var(--footer-light) 40%, var(--footer-mid) 100%);
    border-top: 2px solid var(--silver-line);
  }
  .follow {
    position: absolute; left: 100px; top: 28px; color: var(--footer-text);
  }
  .follow .title { font-size: 28px; font-weight: 500; letter-spacing: 2px; line-height: 1; }
  .follow .sub { font-size: 13px; letter-spacing: 1px; margin-top: 6px; }
  .social-list { position: absolute; left: 370px; top: 36px; display: flex; gap: 30px; }
  .social-dot { width: 36px; height: 36px; border-radius: 50%; background: var(--footer-text); }
</style>
</head>
<body>
  <div class="card">
    <div class="brand">
      <div class="brand-mark"></div>
      <div class="brand-name">
        <span class="primary">FLOWMARK</span>
        <span class="secondary">ENGINEERING</span>
      </div>
    </div>

    <div class="contact-band">
      <div class="contact-item" style="left:205px">
        <div class="icon">
          <svg viewBox="0 0 56 56"><circle cx="28" cy="20" r="10" fill="var(--icon-glyph)"/><path d="M10 48c0-11 8-17 18-17s18 6 18 17z" fill="var(--icon-glyph)"/></svg>
        </div>
        <div class="person-name">DANIEL HART</div>
        <div class="person-role">GENERAL MANAGER</div>
      </div>
      <div class="contact-item" style="left:553px">
        <div class="icon">
          <svg viewBox="0 0 56 56" fill="none" stroke="var(--icon-glyph)" stroke-width="3"><circle cx="28" cy="28" r="22"/><ellipse cx="28" cy="28" rx="10" ry="22"/><path d="M6 28h44M10 17h36M10 39h36M28 6v44"/></svg>
        </div>
        <div class="contact-line">d.hart@flowmark.com</div>
        <div class="contact-line">www.flowmarkeng.com</div>
      </div>
      <div class="contact-item" style="left:901px">
        <div class="icon">
          <svg viewBox="0 0 56 56"><rect x="17" y="6" width="22" height="44" rx="4" fill="var(--icon-glyph)"/><rect x="20" y="12" width="16" height="28" fill="var(--icon-fill)"/><circle cx="28" cy="45" r="2" fill="var(--icon-fill)"/></svg>
        </div>
        <div class="contact-line">012 555 0147</div>
        <div class="contact-line">012 555 0147</div>
      </div>
    </div>

    <div class="footer">
      <div class="follow">
        <div class="title">FOLLOW US</div>
        <div class="sub">ON SOCIAL NETWORKS</div>
      </div>
      <div class="social-list">
        <span class="social-dot"></span>
        <span class="social-dot"></span>
        <span class="social-dot"></span>
        <span class="social-dot"></span>
      </div>
    </div>
  </div>
</body>
</html>
```